Business card design for my company.
I would like the card's background colour to be black. You can also see our web site to get an idea of our brand. https://www.tmwhomecrafting.com.au/
- Name
- Email

```html
<!DOCTYPE html>
<html lang="en">
<head>
<meta charset="utf-8">
<title>TMW Home Crafting – Business Card</title>
<link href="https://fonts.googleapis.com/css2?family=Poppins:wght@300;400;500&display=swap" rel="stylesheet">
<style>
  :root {
    --page-bg: #3a3a3b;
    --card-front: #333435;
    --card-back: #353637;
    --pattern-tone: #3f4041;
    --brand-green: #2e9a4c;
    --text-light: #e9e9e9;
    --text-soft: #cfcfcf;
  }
  * { box-sizing: border-box; margin: 0; padding: 0; }
  html, body {
    width: 1200px;
    height: 1043px;
    overflow: hidden;
    background: var(--page-bg);
    font-family: "Poppins", sans-serif;
  }
  .card {
    position: absolute;
    left: 200px;
    width: 804px;
    height: 430px;
    box-shadow: 0 10px 22px rgba(0,0,0,0.45);
  }
  .card-front { top: 102px; background: var(--card-front); }
  .card-back  { top: 582px; background: var(--card-back); overflow: hidden; }

  .brand-name {
    position: absolute;
    color: var(--text-light);
    font-weight: 500;
    letter-spacing: 1px;
    line-height: 1.05;
  }
  .card-front .brand-name { left: 73px; top: 74px; font-size: 20px; }
  .card-back .brand-name  { left: 465px; top: 292px; font-size: 30px; }

  .person {
    position: absolute;
    left: 82px;
    top: 310px;
    text-align: right;
  }
  .person-name {
    font-size: 28px;
    font-weight: 300;
    color: var(--text-light);
    line-height: 1.1;
  }
  .person-name .first { color: var(--brand-green); }
  .person-role {
    font-size: 17px;
    font-weight: 300;
    color: var(--text-soft);
    margin-top: 2px;
  }

  .divider {
    position: absolute;
    left: 397px;
    top: 313px;
    width: 3px;
    height: 80px;
    background: var(--brand-green);
  }

  .contact-list {
    position: absolute;
    left: 428px;
    top: 314px;
    list-style: none;
  }
  .contact-list li {
    display: flex;
    align-items: center;
    height: 23px;
    font-size: 17px;
    font-weight: 300;
    color: var(--text-light);
  }
  .contact-list svg {
    width: 14px;
    height: 14px;
    margin-right: 18px;
    fill: var(--brand-green);
    flex: none;
  }

  .pattern-field {
    position: absolute;
    inset: 0;
    background: linear-gradient(180deg, var(--pattern-tone), var(--card-back));
  }
</style>
</head>
<body>

<section class="card card-front">
  <div class="brand-name">TMW<br>HOME CRAFTING</div>

  <div class="person">
    <p class="person-name"><span class="first">Liam</span> Fenwick</p>
    <p class="person-role">General Manager</p>
  </div>

  <div class="divider"></div>

  <ul class="contact-list">
    <li>
      <svg viewBox="0 0 24 24" aria-hidden="true"><path d="M6.6 10.8a15.2 15.2 0 0 0 6.6 6.6l2.2-2.2c.3-.3.7-.4 1-.2 1.1.4 2.3.6 3.6.6.6 0 1 .4 1 1V20c0 .6-.4 1-1 1A17 17 0 0 1 3 4c0-.6.4-1 1-1h3.5c.6 0 1 .4 1 1 0 1.3.2 2.5.6 3.6.1.3 0 .7-.2 1z"/></svg>
      0400 555 123
    </li>
    <li>
      <svg viewBox="0 0 24 24" aria-hidden="true"><path d="M2 5h20v14H2z"/></svg>
      info@tmwhomecrafting.com.au
    </li>
    <li>
      <svg viewBox="0 0 24 24" aria-hidden="true"><path d="M12 2a7 7 0 0 0-7 7c0 5.2 7 13 7 13s7-7.8 7-13a7 7 0 0 0-7-7zm0 9.5A2.5 2.5 0 1 1 12 6.5a2.5 2.5 0 0 1 0 5z"/></svg>
      Launceston, Tasmania, Australia
    </li>
  </ul>
</section>

<section class="card card-back">
  <div class="pattern-field" role="img" aria-label="Faint repeating brand pattern covering the card back"></div>
  <div class="brand-name">TMW<br>HOME CRAFTING</div>
</section>

</body>
</html>
```